Blow Dry Bar Business Cards

These cards must be eye catching and modern.
You must be willing to work fast and make changes.

Winner will be offered other projects

Files 1 THIS IS THE STYLE CARDS I AM INTRESTED IN!!!
Please be creative, I am paying for my own eye catching design. I need files to be nexa press ready.

COLORS THAT ARE PAINTED INSIDE MY SHOP:
- - - http://www.quorvelpaint.example/en/explore-colors/painter/color-selector.html?colors=4007-3C

- - - http://www.brandivex.example/color/paint-colors/hidden-corridor-d58-2

I want the business cards sleek and modern if you use the logo please correct imperfections. I added the part that says Blow Dry Bar (see website).
Do not be afraid to separate the blow dryer from the name to make the cards look like the file with the pink elephant.

SHOULD INCLUDE
*Blow Dryer (we are a blow dry bar not a salon we do not cut or color so do not include sheers of any kind)
*BUSINESS NAME: Simply Swept Upward - Blow Dry Bar (PLEASE SEE MY WEBSITE)
* Website: SIMPLYSWEPTUPWARD.EXAMPLE
*Phone number (555) 014-2763
Updates

Nexa press said it can be submitted in JPG

http://www.brandivex.example/color/paint-colors/hidden-corridor-d58-2 http://www.quorvelpaint.example/en/explore-colors/painter/color-selector.html?colors=4007-3C ^^^^ These links will take you to the color paint that is painted inside my shop.

Target Market(s)

AGES 18 - 55 WOMEN
HIGH END MARKET

Industry/Entity Type

Salon

Requirements
Must have
• SEE COLOR EXAMPLE FILE
BLOW DRYER
UNIQUE
I LIKE THE CARD WITH THE PINK ELEPHANT THE BEST
Nice to have
• BE AS CREATIVE AND MODERN AS POSSIBLE DO NOT COPY ANY OF THE CARDS BELOW.
Should not have
• SCISSORS
PINK

```html
<!DOCTYPE html>
<html lang="en">
<head>
<meta charset="utf-8">
<title>Simply Swept Upward – Business Card</title>
<link rel="stylesheet" href="https://fonts.googleapis.com/css2?family=Arimo:wght@400&display=swap">
<style>
  :root {
    --page: #d9d2c7;
    --card-dark: #1b1b1b;
    --card-mid: #2a2a2a;
    --gold: #f5b21c;
    --edge: #0e0e0e;
  }
  * { margin: 0; padding: 0; box-sizing: border-box; }
  html, body {
    width: 1200px;
    height: 870px;
    overflow: hidden;
    background: var(--page);
  }
  .canvas {
    position: relative;
    width: 1200px;
    height: 870px;
    display: flex;
    justify-content: center;
    align-items: center;
    gap: 60px;
    font-family: "Arimo", "Helvetica Neue", Arial, sans-serif;
    color: var(--gold);
  }
  .card {
    position: relative;
    width: 420px;
    height: 735px;
    border-radius: 4px;
    background: linear-gradient(160deg, var(--card-mid) 0%, var(--card-dark) 55%, var(--edge) 100%);
    box-shadow: 0 2px 6px rgba(0,0,0,0.25);
    overflow: hidden;
  }
  .card-texture {
    position: absolute;
    inset: 0;
    background: linear-gradient(135deg, rgba(255,255,255,0.05), rgba(0,0,0,0.15));
  }
  .brand {
    position: absolute;
    display: flex;
    align-items: center;
    gap: 12px;
    font-size: 34px;
    font-weight: 400;
    white-space: nowrap;
  }
  .brand-dot {
    width: 18px;
    height: 18px;
    border-radius: 50%;
    background: var(--gold);
    flex: none;
  }
  .card-front .brand { top: 130px; left: 0; right: 0; justify-content: center; }
  .service {
    position: absolute;
    top: 250px;
    left: 0; right: 0;
    text-align: center;
    font-size: 40px;
    letter-spacing: 0.5px;
  }
  .contact {
    position: absolute;
    top: 470px;
    left: 0; right: 0;
    text-align: center;
    list-style: none;
    font-size: 19px;
    line-height: 1.55;
    text-transform: uppercase;
  }
  .contact .phone { font-size: 20px; }
  .contact .address { margin-top: 14px; line-height: 1.3; }
  .card-back .brand { bottom: 90px; right: 36px; font-size: 30px; }
</style>
</head>
<body>
<main class="canvas">
  <section class="card card-front">
    <div class="card-texture" role="img" aria-label="Dark woven linen texture"></div>
    <div class="brand"><span class="brand-name">Simply Swept Upward</span><span class="brand-dot"></span></div>
    <p class="service">Blow Dry Bar</p>
    <ul class="contact">
      <li class="phone">(555) 014-2763</li>
      <li class="website">SIMPLYSWEPTUPWARD.EXAMPLE</li>
      <li class="email">INFO@SIMPLYSWEPTUPWARD.EXAMPLE</li>
      <li class="address">412 Marsh Hollow Drive Suite 11<br>Fernvale, Texas 70012</li>
    </ul>
  </section>

  <section class="card card-back">
    <div class="card-texture" role="img" aria-label="Dark woven linen texture"></div>
    <div class="brand"><span class="brand-name">Simply Swept Upward</span><span class="brand-dot"></span></div>
  </section>
</main>
</body>
</html>
```